Business Card (double-sided) and Stationary Design for dental office

1) Business Card Design: We need a business card design for a dental specialty office.
Texts should contain:
The name of our office "Brindle Oaks Orthodontics"
Tagline: "Specialist in Orthodontic and Maxillofacial Orthopedics"
Tag line: "Creating "Tolvering" smiles for Children and Adults"
Doctor name: "Doctor Name"
Office Address:
"123 Street Name
City, State Zip code"
Office email address: office@brindleoaksortho.com
Website: www.brindleoaksortho.com

We will provide the full office address once the design is selected
Theme: beach, paradise, coastal, wave
We would like to have some creativity in design. Some acceptable ideas: front page: logo and office name. Back page: more detail information, and map to office in form of an island. Please see sample from our other location, but you DON'T HAVE TO USE OR COPY THE SAME CONCEPT.

IF POSSIBLE, PLEASE SUBMIT AT LEAST TWO CONCEPTS: ONE WITH THE BACK LOOKING SIMILAR TO WHAT IS IN THE SAMPLE, AND ONE DIFFERENT.

Color: designer to choose. We have different shade of blues and sand color in our office. Please see logo.

2) Please also design a matching set of stationary that compliment the business card and our logo.

Target Market(s)

Dental

Contact Information for Business Card

See descriptions

Font styles to use
Other font styles liked:
• Matching texts in logo

Colors
0054AA
0677BA
7BADD7
CADEEF
E8F1F8
0094D4
00A9DD
6FCCEA
C7EBF8
E9F6FB
00AB8E
00BBA5
67D7C9
C6EFE9
E9F9F6

Requirements
Must have
• Double-sided
Nice to have
• Beach coastal theme
Should not have
• Any shape or drawing of of tooth or teeth. We don’t need these. You don't necessarily have to just cut and paste the logo art and text as a whole, you have the liberty to rearrange the text.

```html
<!DOCTYPE html>
<html lang="en">
<head>
<meta charset="utf-8">
<title>Brindle Oaks Orthodontics – Envelope</title>
<link href="https://fonts.googleapis.com/css2?family=Montserrat:wght@700&family=Roboto+Slab:wght@400;600&display=swap" rel="stylesheet">
<style>
  :root {
    --paper: #ffffff;
    --ink: #0b0b0b;
    --frame: #111111;
    --flap-top: #f6f9f8;
    --flap-bottom: #e9f3f0;
    --flap-edge: #f7f1f2;
    --sea-light: #f3f8f9;
    --sea-mid: #e6f1f4;
    --sea-deep: #d3e8ef;
    --brand-teal: #447a8e;
  }
  html, body {
    margin: 0;
    padding: 0;
    width: 1200px;
    height: 825px;
    overflow: hidden;
    background: var(--paper);
  }
  .envelope {
    position: relative;
    width: 1200px;
    height: 825px;
    background: var(--paper);
    overflow: hidden;
  }
  .envelope-art {
    position: absolute;
    inset: 0;
  }
  .envelope-frame {
    position: absolute;
    left: 11px;
    top: 9px;
    width: 1176px;
    height: 805px;
    border: 1px solid var(--frame);
    box-sizing: border-box;
  }
  .brand-mark {
    position: absolute;
    left: 56px;
    top: 582px;
    width: 156px;
    text-align: center;
  }
  .brand-mark__circle {
    display: block;
    width: 96px;
    height: 96px;
    margin: 0 auto 10px;
    border-radius: 50%;
    background: var(--brand-teal);
  }
  .brand-mark__name {
    font-family: "Roboto Slab", serif;
    font-weight: 600;
    font-size: 17px;
    color: var(--brand-teal);
  }
  .sender {
    position: absolute;
    left: 245px;
    top: 576px;
    color: var(--ink);
  }
  .sender__office {
    margin: 0 0 14px;
    font-family: "Montserrat", sans-serif;
    font-weight: 700;
    font-size: 22px;
    letter-spacing: 0.3px;
  }
  .sender__doctor {
    margin: 0 0 12px;
    font-family: "Roboto Slab", serif;
    font-weight: 600;
    font-size: 20px;
    letter-spacing: 0.5px;
  }
  .sender__address,
  .sender__contact {
    margin: 0;
    font-family: "Roboto Slab", serif;
    font-weight: 400;
    font-size: 19px;
    letter-spacing: 0.8px;
  }
  .sender__address { margin-bottom: 10px; }
  .sender__contact { line-height: 25px; }
</style>
</head>
<body>
<div class="envelope">
  <svg class="envelope-art" width="1200" height="825" viewBox="0 0 1200 825" aria-hidden="false">
    <defs>
      <linearGradient id="flapFill" x1="0" y1="0" x2="0" y2="1">
        <stop offset="0" stop-color="var(--flap-top)"/>
        <stop offset="1" stop-color="var(--flap-bottom)"/>
      </linearGradient>
      <linearGradient id="seaFill" x1="0" y1="0" x2="0.3" y2="1">
        <stop offset="0" stop-color="var(--sea-light)"/>
        <stop offset="0.6" stop-color="var(--sea-mid)"/>
        <stop offset="1" stop-color="var(--sea-deep)"/>
      </linearGradient>
    </defs>
    <path class="envelope-flap-shadow" d="M14 10 L600 392 L1186 10 Z" fill="var(--flap-edge)"/>
    <path class="envelope-flap" d="M14 10 L600 385 L1186 10 Z" fill="url(#flapFill)"/>
    <path class="sea-foam" role="img" aria-label="Soft photograph of sea foam and shallow water rising toward the right"
      d="M0 556 C60 540 120 535 190 528 C260 522 330 528 390 538 C440 540 470 500 520 470 C560 452 610 440 650 425 C690 410 720 400 760 395 C810 390 860 370 920 360 C960 350 1000 340 1010 320 C1030 305 1080 310 1110 316 C1150 330 1170 360 1200 380 L1200 825 L0 825 Z"
      fill="url(#seaFill)"/>
  </svg>

  <div class="envelope-frame"></div>

  <div class="brand-mark">
    <span class="brand-mark__circle"></span>
    <span class="brand-mark__name">Brindle Oaks</span>
  </div>

  <div class="sender">
    <p class="sender__office">BRINDLE OAKS ORTHODONTICS</p>
    <p class="sender__doctor">DOCTOR NAME</p>
    <p class="sender__address">123 Street Name City, State Zip code</p>
    <p class="sender__contact">office@brindleoaksortho.com<br>www.brindleoaksortho.com</p>
  </div>
</div>
</body>
</html>
```